Need Web Design for Business Process Outsourcing Company (Quorvane)

Quorvane is a business process outsourcing company. Need a simple site similar to http://www.tallowbrinkhire.com/ but with a more professional and credible look. New to the process; not sure where to start and comparing my options. Please let me know what my options are if I choose to go with you. Logo is attached for your reference. Please use same colorway

Reason: I want the final product to be coded. Please confirm you will be able to code final design.

Industry/Entity Type

Business

Coding

Coded - Design and coding required

```html
<!DOCTYPE html>
<html lang="en">
<head>
<meta charset="utf-8">
<title>Quorvane Services</title>
<link href="https://fonts.googleapis.com/css2?family=Oswald:wght@500;600;700&family=Roboto:wght@400;500;700&display=swap" rel="stylesheet">
<style>
:root{
  --blue:#1b8fd8;
  --blue-dark:#0f63a8;
  --navy:#0c2f5e;
  --navy-deep:#08224a;
  --ink:#1d2630;
  --text:#5a6570;
  --light:#f1f4f8;
  --white:#ffffff;
}
*{box-sizing:border-box;margin:0;padding:0}
html,body{width:1200px;height:3548px;overflow:hidden}
body{font-family:"Roboto",Arial,sans-serif;color:var(--text);background:var(--white);font-size:15px;line-height:1.6}
h1,h2,h3{font-family:"Oswald","Arial Narrow",sans-serif;color:var(--ink);font-weight:600}
.btn{display:inline-block;background:var(--blue);color:var(--white);font-family:"Roboto",Arial,sans-serif;font-weight:500;font-size:15px;padding:12px 26px;border-radius:3px;letter-spacing:.5px}

/* header + hero */
.hero{position:relative;height:680px;overflow:hidden}
.hero-photo{position:absolute;inset:0;background:linear-gradient(180deg,#9fc3e0 0%,#6f95b8 45%,#3d5f83 100%)}
.hero-photo::after{content:"";position:absolute;inset:0;background:linear-gradient(90deg,rgba(20,40,70,.25),rgba(255,255,255,.08) 50%,rgba(20,40,70,.3))}
.site-header{position:absolute;top:0;left:0;right:0;height:82px;display:flex;align-items:center;justify-content:space-between;padding:0 40px;background:rgba(8,34,74,.55);z-index:2}
.brand{display:flex;align-items:center;gap:10px;color:var(--white);font-weight:700;font-size:30px}
.brand-mark{width:30px;height:30px;background:var(--blue)}
.nav{display:flex;gap:4px}
.nav a{color:var(--white);font-size:14px;font-weight:500;padding:10px 14px;text-decoration:none}
.nav a.active{background:var(--blue)}
.hero-arrow{position:absolute;top:370px;width:36px;height:36px;border-radius:50%;background:rgba(0,0,0,.3);z-index:2}
.hero-arrow.left{left:10px}.hero-arrow.right{right:10px}
.hero-copy{position:absolute;top:280px;left:0;right:0;text-align:center;z-index:2}
.hero-copy h1{font-size:72px;color:var(--ink);letter-spacing:1px;line-height:1.1}
.hero-copy p{width:760px;margin:14px auto 26px;color:var(--ink);font-size:16px}

/* services strip */
.services{display:grid;grid-template-columns:repeat(5,192px);justify-content:center;background:var(--blue)}
.service{height:192px;display:flex;flex-direction:column;align-items:center;justify-content:center;gap:18px;color:var(--white);font-weight:500;font-size:15px;border-right:1px solid rgba(255,255,255,.25);background:rgba(8,60,120,.35)}
.service.active{background:var(--blue);color:var(--navy)}
.service-text{display:grid;grid-template-columns:repeat(5,192px);justify-content:center}
.service-text p{height:140px;padding:24px 18px 0;font-size:13px;text-align:center;border-right:1px solid #e1e6ec;position:relative}
.service-text p::after{content:"";position:absolute;left:50%;bottom:22px;width:10px;height:10px;border-right:2px solid var(--blue);border-bottom:2px solid var(--blue);transform:translateX(-50%) rotate(45deg)}

/* welcome */
.welcome{height:440px;text-align:center;padding-top:90px}
.welcome h2{font-size:44px}
.welcome p{width:1000px;margin:10px auto 0;font-size:14px}
.welcome .btn{margin-top:26px}

/* features */
.features{height:320px;background:var(--light);display:flex;align-items:center;padding:0 80px;gap:40px}
.feature-grid{display:grid;grid-template-columns:380px 380px;gap:40px 30px}
.feature{display:flex;gap:18px}
.feature-icon{flex:none;width:90px;height:90px;background:var(--white);border:1px solid #dbe2ea;display:flex;align-items:center;justify-content:center}
.feature h3{font-family:"Roboto",Arial,sans-serif;font-size:16px;font-weight:700;color:var(--navy);margin-bottom:6px}
.feature p{font-size:13px}
.feature-brand{margin-left:auto;display:flex;align-items:center;gap:16px;color:var(--blue-dark);font-weight:700;font-size:40px}
.feature-brand span{width:60px;height:60px;background:var(--blue-dark)}

/* global presence */
.global{height:420px;background:linear-gradient(90deg,var(--blue-dark),var(--blue) 60%,#2aa3ea);display:flex;align-items:center;padding:0 70px;gap:50px}
.map{width:440px;height:280px;border-radius:50%/40%;background:radial-gradient(ellipse at center,rgba(255,255,255,.35),rgba(255,255,255,.05) 70%)}
.global h2{color:var(--white);font-family:"Roboto",Arial,sans-serif;font-size:40px;font-weight:500;letter-spacing:1px}
.global p{color:#dcecf9;font-size:14px;width:600px;margin:12px 0 24px}
.btn.ghost{background:transparent;border:1px solid var(--white)}

/* passionate */
.passion{height:420px;display:flex;padding:60px 70px 0;gap:30px;position:relative}
.passion-copy{width:560px}
.passion h2{font-size:36px;line-height:1.2;color:var(--navy)}
.passion p{font-size:14px;margin:16px 0 24px}
.passion-photo{flex:1;height:340px;background:linear-gradient(120deg,#ffffff,#e8edf3 40%,#c9a88c 75%,#7a5b48)}

/* news */
.news{height:460px;padding-top:30px}
.news h2{font-size:40px;text-align:center;margin-bottom:26px}
.news-grid{display:grid;grid-template-columns:repeat(4,250px);gap:30px;justify-content:center}
.news-photo{height:160px}
.n1{background:linear-gradient(135deg,#0e3f7a,#4fa7e0)}
.n2{background:linear-gradient(135deg,#8a8f96,#d3d7dc)}
.n3{background:linear-gradient(135deg,#b9c3cc,#5e6d7a)}
.n4{background:linear-gradient(135deg,#6d8aa3,#dfe5ea)}
.news-card h3{font-family:"Roboto",Arial,sans-serif;font-size:14px;font-weight:700;color:var(--blue);margin-top:12px}
.news-card time{display:inline-block;background:var(--navy);color:var(--white);font-size:11px;padding:2px 8px;margin:6px 0}
.news-card p{font-size:13px}

/* footer */
.site-footer{height:380px;background:var(--navy);display:grid;grid-template-columns:340px 380px 360px;gap:30px;padding:50px 40px 0;color:#b8c8dc;font-size:13px}
.site-footer h4{color:var(--white);font-weight:500;font-size:14px;letter-spacing:1px;margin-bottom:18px}
.footer-brand{display:flex;align-items:center;gap:10px;color:var(--white);font-weight:700;font-size:32px;margin-bottom:16px}
.footer-brand span{width:30px;height:30px;background:var(--blue)}
.site-footer p{margin-bottom:12px}
.contact-line{display:flex;gap:10px;align-items:center;margin-bottom:12px}
.socials{display:flex;gap:10px;margin-top:10px}
.socials span{width:32px;height:32px;border-radius:50%;background:var(--blue)}
.field{height:34px;background:var(--navy-deep);border:1px solid #1e4777;margin-bottom:10px;padding:7px 10px;color:#8ea6c4}
.field.msg{height:70px}
.site-footer .btn{padding:9px 26px}
.copyright{height:68px;background:var(--navy-deep);color:#8ea6c4;font-size:12px;text-align:center;line-height:68px}
</style>
</head>
<body>

<section class="hero">
  <div class="hero-photo" role="img" aria-label="Businessman with open arms in front of glass office towers"></div>
  <header class="site-header">
    <div class="brand"><span class="brand-mark"></span>Quorvane</div>
    <nav class="nav">
      <a class="active">HOME</a><a>ABOUT</a><a>SERVICES</a><a>STRATEGY</a><a>EXPERIENCE</a><a>SECURITY</a><a>NEWS</a><a>CONTACT</a>
    </nav>
  </header>
  <span class="hero-arrow left"></span><span class="hero-arrow right"></span>
  <div class="hero-copy">
    <h1>QUORVANE SERVICES</h1>
    <p>Lorem Ipsum is simply dummy text of the printing and typesetting industry. Lorem Ipsum has been the industry's standard dummy text ever since the 1500s, when an unknown</p>
    <span class="btn">CONTACT US KNOW</span>
  </div>
</section>

<section>
  <div class="services">
    <div class="service"><svg width="50" height="50" viewBox="0 0 50 50" fill="none" stroke="#fff" stroke-width="3"><path d="M10 28v-6a15 15 0 0 1 30 0v6"/><rect x="7" y="27" width="8" height="12" fill="#fff"/><rect x="35" y="27" width="8" height="12" fill="#fff"/></svg>CUSTOMER SERVICE</div>
    <div class="service"><svg width="50" height="50" viewBox="0 0 50 50" fill="none" stroke="#fff" stroke-width="3"><path d="M5 10h7l5 22h22l4-15H14"/><circle cx="20" cy="40" r="3" fill="#fff"/><circle cx="36" cy="40" r="3" fill="#fff"/></svg>ECOMMERCE</div>
    <div class="service active"><svg width="50" height="50" viewBox="0 0 50 50" fill="none" stroke="#0c2f5e" stroke-width="3"><rect x="6" y="8" width="38" height="26"/><path d="M18 42h14M25 34v8M12 14l26 14M38 14L12 28"/></svg>CLOUD SERVICES</div>
    <div class="service"><svg width="50" height="50" viewBox="0 0 50 50" fill="none" stroke="#fff" stroke-width="3"><path d="M25 10a11 11 0 0 0-6 20v5h12v-5a11 11 0 0 0-6-20z"/><path d="M20 40h10M25 2v4M8 18h-4M46 18h-4"/></svg>IT SOLUTIONS</div>
    <div class="service"><svg width="54" height="50" viewBox="0 0 54 50" fill="#fff"><circle cx="27" cy="16" r="7"/><circle cx="12" cy="20" r="5"/><circle cx="42" cy="20" r="5"/><path d="M15 42a12 12 0 0 1 24 0z"/><path d="M3 40a9 9 0 0 1 14-7v7zM51 40a9 9 0 0 0-14-7v7z"/></svg>HUMAN RESOURCES</div>
  </div>
  <div class="service-text">
    <p>Lorem Ipsum is simply dummy text of the printing and type setting.</p>
    <p>Lorem Ipsum is simply dummy text of the printing and type setting.</p>
    <p>Lorem Ipsum is simply dummy text of the printing and type setting.</p>
    <p>Lorem Ipsum is simply dummy text of the printing and type setting.</p>
    <p>Lorem Ipsum is simply dummy text of the printing and type setting.</p>
  </div>
</section>

<section class="welcome">
  <h2>WELCOME TO QUORVANE SERVICES</h2>
  <p>Lorem Ipsum is simply dummy text of the printing and typesetting industry. Lorem Ipsum has been the industry's standard dummy text ever since the 1500s, when an unknown printer took a galley of type and scrambled it to make a type specimen book.</p>
  <p>It has survived not only five centuries. Lorem Ipsum is simply dummy text of the printing and typesetting industry. Lorem Ipsum has been the industry's standard dummy text ever since the 1500s, when an unknown printer took a galley of type and scrambled it to make a type specimen book. It has survived not only five centuries.</p>
  <span class="btn">KNOW MORE</span>
</section>

<section class="features">
  <div class="feature-grid">
    <div class="feature">
      <div class="feature-icon"><svg width="50" height="50" viewBox="0 0 50 50" fill="none" stroke="#1b8fd8" stroke-width="4"><circle cx="20" cy="22" r="8"/><path d="M20 6v6M20 32v6M4 22h6M30 22h6"/><circle cx="38" cy="38" r="5"/></svg></div>
      <div><h3>REINVENTING SERVICES</h3><p>Lorem Ipsum is simply dummy text of the printing and typesetting industry. Lorem Ipsum has been the.</p></div>
    </div>
    <div class="feature">
      <div class="feature-icon"><svg width="50" height="50" viewBox="0 0 50 50" fill="#1b8fd8"><rect x="6" y="20" width="12" height="24"/><rect x="20" y="8" width="12" height="36"/><rect x="34" y="26" width="10" height="18"/></svg></div>
      <div><h3>OUR FACILITIES</h3><p>Lorem Ipsum is simply dummy text of the printing and typesetting industry. Lorem Ipsum has been the.</p></div>
    </div>
    <div class="feature">
      <div class="feature-icon"><svg width="54" height="50" viewBox="0 0 54 50" fill="#1b8fd8"><circle cx="14" cy="18" r="5"/><circle cx="27" cy="14" r="6"/><circle cx="40" cy="18" r="5"/><path d="M4 38a10 10 0 0 1 20 0zM16 36a11 11 0 0 1 22 0zM30 38a10 10 0 0 1 20 0z"/></svg></div>
      <div><h3>OUR PEOPLE</h3><p>Lorem Ipsum is simply dummy text of the printing and typesetting industry. Lorem Ipsum has been the.</p></div>
    </div>
    <div class="feature">
      <div class="feature-icon"><svg width="50" height="50" viewBox="0 0 50 50" fill="#1b8fd8"><circle cx="16" cy="16" r="6"/><circle cx="34" cy="16" r="6"/><path d="M4 40a12 12 0 0 1 24 0zM22 40a12 12 0 0 1 24 0z"/></svg></div>
      <div><h3>SUCCESS STORIES</h3><p>Lorem Ipsum is simply dummy text of the printing and typesetting industry. Lorem Ipsum has been the.</p></div>
    </div>
  </div>
  <div class="feature-brand"><span></span>Quorvane</div>
</section>

<section class="global">
  <div class="map" role="img" aria-label="World map showing global office locations"></div>
  <div>
    <h2>GLOBAL PRESENCE</h2>
    <p>Lorem Ipsum is simply dummy text of the printing and typesetting industry. Lorem Ipsum has been the industry's standard dummy text ever since the 1500s, when an unknown printer took a galley of type and scrambled it to make a type specimen book. It has survived not only five centuries, but also the leap into electronic typesetting, remaining essentially unchanged.</p>
    <span class="btn ghost">KNOW MORE</span>
  </div>
</section>

<section class="passion">
  <div class="passion-copy">
    <h2>PASSIONATE ABOUT ENGAGING WITH CLIENTS<br>&amp; GROWING BUSINESS ?</h2>
    <p>Lorem Ipsum is simply dummy text of the printing and typesetting industry. Lorem Ipsum has been the industry's standard dummy text ever since the 1500s, when an unknown printer took a galley of type and scrambled it to make a type specimen book. It has survived not only five centuries, but also the leap into electronic typesetting, remaining essentially unchanged. Lorem Ipsum is simply dummy text of the printing and typesetting industry. Lorem Ipsum has been the industry's standard dummy text ever since the 1500s, when an.</p>
    <span class="btn">APPLY KNOW</span>
  </div>
  <div class="passion-photo" role="img" aria-label="Businesswoman drawing a rising red growth line"></div>
</section>

<section class="news">
  <h2>LATEST NEWS</h2>
  <div class="news-grid">
    <article class="news-card"><div class="news-photo n1" role="img" aria-label="Team working at laptops"></div><h3>LOREM IPSUM IS THE SIMPLE</h3><time>09 Nov 2016</time><p>Lorem Ipsum is simply dummy text of the printing and typesetting industry. Lorem Ipsum has been the.</p></article>
    <article class="news-card"><div class="news-photo n2" role="img" aria-label="Colleagues in a meeting"></div><h3>LOREM IPSUM IS THE SIMPLE</h3><time>10 Nov 2016</time><p>Lorem Ipsum is simply dummy text of the printing and typesetting industry. Lorem Ipsum has been the.</p></article>
    <article class="news-card"><div class="news-photo n3" role="img" aria-label="Business handshake"></div><h3>LOREM IPSUM IS THE SIMPLE</h3><time>11 Nov 2016</time><p>Lorem Ipsum is simply dummy text of the printing and typesetting industry. Lorem Ipsum has been the.</p></article>
    <article class="news-card"><div class="news-photo n4" role="img" aria-label="Hands over a desk with documents"></div><h3>LOREM IPSUM IS THE SIMPLE</h3><time>12 Nov 2016</time><p>Lorem Ipsum is simply dummy text of the printing and typesetting industry. Lorem Ipsum has been the.</p></article>
  </div>
</section>

<footer>
  <div class="site-footer">
    <div>
      <div class="footer-brand"><span></span>Quorvane</div>
      <p>Lorem Ipsum is simply dummy text of the printing and typesetting industry. Lorem Ipsum has been the industry's standard dummy text ever since the 1500s, when an unknown printer.</p>
      <p>Lorem Ipsum is simply dummy text of the printing and typesetting industry. Lorem Ipsum has been the industry's standard dummy.</p>
    </div>
    <div>
      <h4>GET IN TOUCH</h4>
      <div class="contact-line"><svg width="16" height="20" viewBox="0 0 16 20" fill="#1b8fd8"><path d="M8 0a8 8 0 0 0-8 8c0 6 8 12 8 12s8-6 8-12a8 8 0 0 0-8-8zm0 11a3 3 0 1 1 0-6 3 3 0 0 1 0 6z"/></svg><span style="color:#fff;font-weight:500">QUORVANE SERVICES</span></div>
      <p style="padding-left:26px">Lorem Ipsum is simply dummy text of the printing and typesetting industry. Lorem Ipsum has been.</p>
      <div class="contact-line"><svg width="16" height="16" viewBox="0 0 16 16" fill="#1b8fd8"><path d="M3 0l3 4-2 2a10 10 0 0 0 6 6l2-2 4 3-2 3C7 16 0 9 0 2z"/></svg>123 456 7890</div>
      <div class="contact-line"><svg width="16" height="12" viewBox="0 0 16 12" fill="none" stroke="#1b8fd8" stroke-width="2"><rect x="1" y="1" width="14" height="10"/><path d="M1 1l7 6 7-6"/></svg>info@quorvane.com</div>
      <div class="socials"><span></span><span></span><span></span></div>
    </div>
    <div>
      <h4>GET A FREE QUOTE</h4>
      <div class="field">Name*</div>
      <div class="field">Email*</div>
      <div class="field">Phone*</div>
      <div class="field msg">Message</div>
      <span class="btn">SUBMIT</span>
    </div>
  </div>
  <div class="copyright">© QUORVANE SERVICES - 2016 All rights reserved.</div>
</footer>

</body>
</html>
```